Webdesign für Zahnarztpraxis
Zielgruppe
Zahnarztpraxis
Aufgabenstellung
- Klares und übersichtliches Desgin
- Nicht zu verspielt
- Informativ
- Leichte Naviagtion
- Das Design der alten Webseite soll NICHT kopiert werden
- Die Farben Blau und Grün aus dem Logo sollen sich wiederfinden
- Designbeispiele, die dem Kunden gefallen sind https://www.falkmann-ostrup-zahnarztpraxis.de/ und https://www.zahvilkorn.de/

```html
<!DOCTYPE html>
<html lang="de">
<head>
<meta charset="utf-8">
<title>Zahnarztpraxis Kohlmeier – Talbrücken</title>
<link rel="stylesheet" href="https://fonts.googleapis.com/css2?family=Inter:wght@400;500;600;700;800&display=swap">
<style>
:root{
  --green:#6db33f;
  --green-dark:#5a9e2f;
  --teal:#3ea89a;
  --blue:#1e9ad6;
  --ink:#141b2d;
  --text:#4b5565;
  --muted:#8a93a3;
  --page:#f6f8fb;
  --card:#eef2f7;
  --mint:#edf3ea;
  --sage:#eef3ef;
  --line:#dde6ee;
}
*{box-sizing:border-box;margin:0;padding:0}
html,body{width:1200px;height:3062px;overflow:hidden}
body{font-family:"Inter",sans-serif;background:var(--page);color:var(--ink);position:relative}
.abs{position:absolute}

/* Hero */
.hero{position:absolute;left:0;top:0;width:1200px;height:586px;
  background:linear-gradient(90deg,#e4e8e6 0%,#f1f3f0 30%,#f7f8f4 55%,#eef2e6 80%,#e6ebe6 100%)}
.hero-photo{position:absolute;inset:0;
  background:radial-gradient(ellipse at 78% 30%,rgba(220,235,200,.7),transparent 45%),
  radial-gradient(ellipse at 12% 45%,rgba(200,205,210,.55),transparent 40%),
  radial-gradient(ellipse at 72% 75%,rgba(210,180,180,.35),transparent 30%)}
.nav{position:absolute;left:120px;top:20px;width:960px;height:67px;background:rgba(255,255,255,.92);
  border-radius:34px;box-shadow:0 4px 20px rgba(0,0,0,.05)}
.brand{position:absolute;left:22px;top:22px;display:flex;align-items:center;gap:8px;
  font-size:16px;font-weight:700;color:var(--teal)}
.brand-dot{width:18px;height:18px;border-radius:50%;background:var(--blue)}
.nav-links{position:absolute;left:377px;top:25px;display:flex;gap:36px;font-size:12.5px;color:var(--ink)}
.btn{display:inline-flex;align-items:center;justify-content:center;gap:8px;background:var(--green);
  color:#fff;font-weight:600;border-radius:30px;box-shadow:0 6px 14px rgba(109,179,63,.3)}
.nav-cta{position:absolute;right:22px;top:16px;width:84px;height:35px;font-size:12px;font-weight:500}
.eyebrow-pill{position:absolute;left:436px;top:107px;width:329px;height:26px;background:#fff;border-radius:13px;
  font-size:12px;font-weight:700;letter-spacing:1.3px;color:var(--green);display:flex;align-items:center;justify-content:center}
.hero h1{position:absolute;left:0;width:1200px;top:148px;text-align:center;font-size:78px;line-height:80px;
  font-weight:700;letter-spacing:-3px}
.hero h1 .grad{background:linear-gradient(90deg,var(--blue),var(--green));-webkit-background-clip:text;background-clip:text;color:transparent}
.hero-lead{position:absolute;left:320px;width:560px;top:340px;text-align:center;font-size:17px;line-height:27px;color:#2f3848}
.hero-cta{position:absolute;left:495px;top:462px;width:210px;height:52px;font-size:14px;font-weight:500}

/* About */
.label{font-size:10px;font-weight:600;letter-spacing:1.3px;color:var(--muted)}
.about-label{left:87px;top:667px}
.about-title{left:87px;top:690px;font-size:40px;line-height:39px;font-weight:500;letter-spacing:-.8px}
.about-lead{left:87px;top:792px;width:500px;font-size:15.5px;line-height:25px;color:var(--text)}
.about-btn{left:960px;top:805px;width:153px;height:36px;font-size:12px;font-weight:500}
.stat{top:895px;width:504px;height:249px;border-radius:26px;padding:32px 34px}
.stat-green{left:87px;background:var(--mint)}
.stat-blue{left:609px;background:var(--blue);color:#fff}
.stat .big{font-size:50px;font-weight:600;letter-spacing:-1.5px;line-height:1}
.stat-green .big{color:var(--green)}
.stat h3{font-size:17px;font-weight:500;position:absolute;left:34px}
.stat p{position:absolute;left:34px;width:260px;font-size:11.5px;line-height:19px}
.stat-green h3{top:130px;color:var(--green)}.stat-green p{top:160px;color:var(--green)}
.stat-blue h3{top:150px}.stat-blue p{top:180px;color:#e7f4fb}
.stat svg{position:absolute;right:34px;top:28px}
.service{top:1225px;width:329px;height:178px;background:var(--card);border-radius:24px;text-align:center;padding-top:36px}
.service h4{margin-top:20px;font-size:13.5px;font-weight:600}
.service p{margin:10px auto 0;width:250px;font-size:11.5px;line-height:19px;color:var(--text)}
.all-link{left:0;width:1200px;top:1434px;text-align:center;font-size:11.5px;font-weight:500;color:var(--green)}

/* Kompetenz */
.kompetenz{position:absolute;left:0;top:1531px;width:1200px;height:934px;background:var(--sage);border-radius:36px 36px 0 0}
.komp-label{left:87px;top:1612px}
.komp-title{left:87px;top:1637px;font-size:31px;line-height:38px;font-weight:500;letter-spacing:-.6px}
.komp-note{left:793px;top:1675px;width:330px;font-size:11.5px;line-height:19px;color:var(--text)}
.photo{top:1765px;width:500px;height:499px;border-radius:26px;overflow:hidden}
.photo-lab{left:87px;background:linear-gradient(160deg,#c9b48a 0%,#efe9dd 35%,#e9e3d8 60%,#8b8a88 100%)}
.photo-team{left:614px;background:linear-gradient(180deg,#f4f6f8 0%,#e7ecf0 45%,#c9d2db 70%,#eef1f4 100%)}
.photo-caption{position:absolute;left:0;bottom:0;width:100%;height:110px;padding:50px 26px 0;
  background:linear-gradient(180deg,transparent,rgba(20,27,45,.75))}
.photo-caption span{display:block;font-size:9.5px;font-weight:700;letter-spacing:1.2px;color:var(--green)}
.photo-caption strong{display:block;margin-top:6px;font-size:16.5px;font-weight:500;color:#fff}
.round-link{left:560px;top:2306px;width:80px;height:80px;border-radius:50%;border:1px dashed #cdd8cf;
  display:flex;align-items:center;justify-content:center}
.komp-foot{left:0;width:1200px;top:2399px;text-align:center;font-size:10px;line-height:13px;color:var(--muted)}

/* Kontakt */
.contact{position:absolute;left:0;top:2465px;width:1200px;height:597px;
  background:linear-gradient(180deg,#ffffff 0%,#e8f0f8 40%,#cfe2f3 100%)}
.h2-small{font-size:20px;font-weight:500}
.c-left{left:140px;top:2573px}
.c-name{left:140px;top:2628px;font-size:14.5px;font-weight:700}
.c-addr{left:140px;top:2657px;font-size:15px;line-height:23px;color:var(--text)}
.c-row{left:140px;display:flex;align-items:center;gap:12px;font-size:15.5px}
.c-ico{width:38px;height:38px;border-radius:50%;background:#fff;display:flex;align-items:center;justify-content:center}
.c-phone{top:2729px;color:var(--blue)}
.c-mail{top:2782px}
.c-right{left:627px;top:2573px}
.hours{left:627px;top:2627px;width:433px}
.hours li{list-style:none;height:57px;border-bottom:1px solid var(--line);display:flex;justify-content:space-between;align-items:center;font-size:13.5px;font-weight:600}
.hours li span{background:#fff;border-radius:12px;padding:4px 12px;font-size:11.5px;font-weight:400;color:var(--text)}
.hours li.closed{color:var(--muted);font-weight:400}
.hours li.closed span{color:var(--muted)}
.foot-copy{left:140px;top:3007px;font-size:10px;color:var(--text)}
.foot-links{right:140px;top:3007px;display:flex;gap:20px;font-size:10px;color:var(--text)}
</style>
</head>
<body>

<header class="hero">
  <div class="hero-photo" role="img" aria-label="Heller, unscharfer Behandlungsraum der Praxis mit Fenster und Behandlungsstuhl"></div>
  <nav class="nav">
    <div class="brand"><span class="brand-dot"></span>Praxis Kohlmeier</div>
    <div class="nav-links"><span>Praxis</span><span>Leistungen</span><span>Team</span></div>
    <a class="btn nav-cta">Kontakt</a>
  </nav>
  <div class="eyebrow-pill">• ZAHNARZTPRAXIS TALBRÜCKEN</div>
  <h1>Gesunde<br><span class="grad">Zähne &amp; Lächeln</span></h1>
  <p class="hero-lead">Ihre Zahnarztpraxis in Talbrücken. Wir verbinden moderne Zahnmedizin mit persönlicher Fürsorge und einem eigenen Dentallabor.</p>
  <a class="btn hero-cta">Termin vereinbaren <svg width="10" height="10" viewBox="0 0 10 10"><path d="M1 5h8M6 2l3 3-3 3" stroke="#fff" stroke-width="1.3" fill="none"/></svg></a>
</header>

<div class="abs label about-label">01 — ÜBER UNS</div>
<h2 class="abs about-title">Bezahlbare Zahngesundheit<br>für Ihre Familie</h2>
<p class="abs about-lead">Willkommen in unserer Praxis &amp; Dentallabor. Unser Fokus liegt auf der Prävention und Individualprophylaxe für jede Altersgruppe.</p>
<a class="abs btn about-btn">Mehr über uns <svg width="9" height="9" viewBox="0 0 10 10"><path d="M1 5h8M6 2l3 3-3 3" stroke="#fff" stroke-width="1.3" fill="none"/></svg></a>

<div class="abs stat stat-green">
  <div class="big">100%</div>
  <svg width="90" height="96" viewBox="0 0 90 96"><path d="M38 10l32 12v24c0 20-14 34-32 40C20 80 6 66 6 46V22z" fill="none" stroke="#d8dfd6" stroke-width="7"/><path d="M25 48l10 10 18-20" fill="none" stroke="#d8dfd6" stroke-width="6"/><path d="M72 6v14M65 13h14" stroke="#b9d9a3" stroke-width="2"/></svg>
  <h3>Prävention</h3>
  <p>Vorsorge statt Nachsorge. Wir setzen auf langfristigen Zahnerhalt durch individuelle Prophylaxe.</p>
</div>
<div class="abs stat stat-blue">
  <div class="big">EN</div>
  <svg width="96" height="96" viewBox="0 0 96 96" fill="none" stroke="rgba(255,255,255,.28)" stroke-width="6"><path d="M8 18h44M30 10v8M16 18c4 16 14 28 28 34M44 18c-4 16-14 28-30 36"/><path d="M46 88l18-44 18 44M52 74h24"/><path d="M80 6v14M73 13h14" stroke="rgba(255,255,255,.7)" stroke-width="2"/></svg>
  <h3>Bilingual</h3>
  <p>Wir beraten und behandeln Sie auch fließend auf Englisch. We speak English fluently.</p>
</div>

<div class="abs service" style="left:87px">
  <svg width="26" height="26" viewBox="0 0 24 24" fill="none" stroke="#141b2d" stroke-width="1.8" stroke-linecap="round"><path d="M5 3v6a5 5 0 0010 0V3"/><path d="M10 14v2a4 4 0 008 0v-3"/><circle cx="18" cy="11" r="2"/></svg>
  <h4>Diagnostik</h4><p>Fundierte Analyse für die beste Behandlungsstrategie.</p>
</div>
<div class="abs service" style="left:436px">
  <svg width="26" height="26" viewBox="0 0 24 24" fill="none" stroke="#141b2d" stroke-width="1.8" stroke-linejoin="round"><path d="M10 4l1.8 5.2L17 11l-5.2 1.8L10 18l-1.8-5.2L3 11l5.2-1.8z"/><path d="M18 2v4M16 4h4M19 17v4M17 19h4"/></svg>
  <h4>Reinigung</h4><p>Professionelle Reinigung für ein gesundes Zahnfleisch.</p>
</div>
<div class="abs service" style="left:784px">
  <svg width="26" height="26" viewBox="0 0 24 24" fill="none" stroke="#141b2d" stroke-width="1.8" stroke-linejoin="round"><path d="M3 7l4.5 4L12 5l4.5 6L21 7l-2 11H5z"/><path d="M5 21h14"/></svg>
  <h4>Prothetik</h4><p>Hochwertiger Zahnersatz für Funktion und Ästhetik.</p>
</div>
<div class="abs all-link">Alle Leistungen ansehen &nbsp;→</div>

<section class="kompetenz"></section>
<div class="abs label komp-label">02 — KOMPETENZ</div>
<h2 class="abs komp-title">Ein gesundes Lächeln beginnt<br>hier</h2>
<p class="abs komp-note">Unser eigenes Praxislabor und kompetentes Team sorgen für kurze Wege und optimale Ergebnisse.</p>
<div class="abs photo photo-lab" role="img" aria-label="Zahnärztin behandelt einen Patienten im Behandlungsraum">
  <div class="photo-caption"><span>LABOR</span><strong>Praxislabor &amp; Behandlungsräume</strong></div>
</div>
<div class="abs photo photo-team" role="img" aria-label="Gruppenbild des Praxisteams in weißer Kleidung im Behandlungsraum"></div>
<div class="abs round-link"><svg width="14" height="14" viewBox="0 0 14 14"><path d="M3 11L11 3M5 3h6v6" stroke="#9aa5b1" stroke-width="1.2" fill="none"/></svg></div>
<p class="abs komp-foot">Kompetente Zahnmedizin und Prophylaxe für ein<br>strahlendes, gesundes Lächeln.</p>

<section class="contact"></section>
<h2 class="abs h2-small c-left">Kontakt &amp; Termin</h2>
<div class="abs c-name">Zahnarztpraxis Kohlmeier</div>
<p class="abs c-addr">Lindenweg 14<br>09217 Talbrücken</p>
<div class="abs c-row c-phone"><span class="c-ico"><svg width="16" height="16" viewBox="0 0 24 24" fill="none" stroke="#1e9ad6" stroke-width="1.8"><path d="M5 3h4l2 5-2.5 1.5a11 11 0 006 6L16 13l5 2v4a2 2 0 01-2 2A16 16 0 013 5a2 2 0 012-2z"/></svg></span>03741-58204</div>
<div class="abs c-row c-mail"><span class="c-ico"><svg width="15" height="15" viewBox="0 0 24 24" fill="none" stroke="#8a93a3" stroke-width="1.8"><rect x="3" y="5" width="18" height="14" rx="2"/><path d="M3 7l9 6 9-6"/></svg></span>info@zahnarztpraxis-kohlmeier.de</div>

<h2 class="abs h2-small c-right">Öffnungszeiten</h2>
<ul class="abs hours">
  <li>Montag<span>9:00 - 13:00 &amp; 14:00 - 19:00</span></li>
  <li>Dienstag<span>9:00 - 13:00 &amp; 14:00 - 19:00</span></li>
  <li>Mittwoch<span>9:00 - 14:00</span></li>
  <li class="closed">Donnerstag<span>Geschlossen</span></li>
  <li>Freitag<span>9:00 - 13:00</span></li>
</ul>

<div class="abs foot-copy">© 2025 Zahnarztpraxis Kohlmeier. Alle Rechte vorbehalten.</div>
<div class="abs foot-links"><span>Impressum</span><span>Datenschutz</span><span>Note</span></div>

</body>
</html>
```